BUSINESS CARD - HALLORAN FIELD SERVICES

I would like to create a business card for my fertilizer spreading business. I would like to incorporate my existing logo and also a description of the services offered. The business card will be given to farmers so must be kept simple but effective. It will also be left in stores so much also be eye catching in order to stand out from other cards.

Target Market(s)

FARMERS

Requirements
Must have
• FRONT OF CARD = EXISTING LOGO + "CUSTOMISED SPREADING" below the logo

REAR Of CARD = SERVICES OFFERED AND CONTACT DETAILS

- Bulk fertilizer including Lime, Gypsum, Manure & Compost
- Granular fertilizer including Single Super, Urea, Gran-am, & Custom Blends
- Modern equipment - Autosteer & Variable Rate Capable
- Friendly & Reliable Service
- Contact Gus: 0417 552 308
Nice to have
• utilize same color scheme as existing logo

```html
<!DOCTYPE html>
<html lang="en">
<head>
<meta charset="utf-8">
<title>Halloran Field Services – Business Card</title>
<link rel="stylesheet" href="https://fonts.googleapis.com/css2?family=Lato:wght@400;700;900&display=swap">
<style>
  :root {
    --bg: #3a3c40;
    --card: #050505;
    --orange: #f7941d;
    --grey: #5c5c5c;
    --text-grey: #7a7a7a;
  }
  html, body {
    margin: 0;
    padding: 0;
    width: 1200px;
    height: 900px;
    overflow: hidden;
    background: var(--bg);
    font-family: "Lato", sans-serif;
  }
  .canvas {
    position: relative;
    width: 1200px;
    height: 900px;
  }
  .card {
    position: absolute;
    width: 620px;
    height: 354px;
    background: var(--card);
    border-radius: 18px;
    overflow: hidden;
  }
  .card-front { left: 150px; top: 60px; }
  .card-back  { left: 430px; top: 486px; }

  /* Front */
  .brand {
    position: absolute;
    inset: 0;
    display: flex;
    flex-direction: column;
    align-items: center;
    justify-content: center;
  }
  .brand-mark {
    width: 136px;
    height: 136px;
    border-radius: 50%;
    background: var(--grey);
    margin-bottom: 20px;
  }
  .brand-name {
    font-weight: 900;
    font-size: 40px;
    letter-spacing: 0.5px;
    color: var(--grey);
    margin: 0;
    line-height: 1;
  }
  .tagline {
    display: flex;
    align-items: center;
    gap: 12px;
    width: 500px;
    margin-top: 14px;
  }
  .tagline .rule {
    flex: 1;
    height: 3px;
    background: var(--orange);
  }
  .tagline p {
    margin: 0;
    font-weight: 900;
    font-size: 20px;
    letter-spacing: 5px;
    color: var(--orange);
    white-space: nowrap;
  }

  /* Back */
  .tab {
    position: absolute;
    left: -8px;
    top: 34px;
    width: 18px;
    height: 46px;
    border-radius: 9px;
    background: var(--orange);
  }
  .person {
    position: absolute;
    left: 30px;
    top: 30px;
  }
  .person-name {
    margin: 0;
    font-weight: 700;
    font-size: 24px;
    color: var(--orange);
    line-height: 1;
  }
  .person-role {
    margin: 4px 0 0;
    font-size: 15px;
    color: var(--text-grey);
    letter-spacing: 0.5px;
  }
  .phone {
    position: absolute;
    right: 32px;
    top: 34px;
    display: flex;
    align-items: center;
    gap: 8px;
    font-size: 16px;
    color: var(--text-grey);
    letter-spacing: 1px;
  }
  .phone svg { width: 18px; height: 18px; }
  .services-heading {
    position: absolute;
    left: 40px;
    right: 40px;
    top: 130px;
    display: flex;
    align-items: center;
    gap: 12px;
  }
  .services-heading .rule {
    flex: 1;
    height: 3px;
    background: var(--orange);
  }
  .services-heading h2 {
    margin: 0;
    font-weight: 900;
    font-size: 28px;
    letter-spacing: 6px;
    color: var(--orange);
  }
  .service-list {
    position: absolute;
    left: 60px;
    right: 30px;
    top: 188px;
    margin: 0;
    padding: 0;
    list-style: none;
    font-size: 15px;
    line-height: 22px;
    color: var(--text-grey);
  }
  .service-list li {
    position: relative;
    padding-left: 20px;
  }
  .service-list li::before {
    content: "";
    position: absolute;
    left: 0;
    top: 5px;
    width: 12px;
    height: 12px;
    border-radius: 50%;
    background: var(--orange);
  }
</style>
</head>
<body>
<main class="canvas">

  <section class="card card-front" aria-label="Card front">
    <div class="brand">
      <div class="brand-mark"></div>
      <h1 class="brand-name">HALLORAN FIELD SERVICES</h1>
      <div class="tagline">
        <span class="rule"></span>
        <p>CUSTOMISED SPREADING</p>
        <span class="rule"></span>
      </div>
    </div>
  </section>

  <section class="card card-back" aria-label="Card back">
    <div class="tab"></div>
    <div class="person">
      <p class="person-name">Gus</p>
      <p class="person-role">CEO/ General Manager</p>
    </div>
    <div class="phone">
      <svg viewBox="0 0 24 24" aria-hidden="true">
        <path fill="#f7941d" d="M6.6 10.8a15.1 15.1 0 0 0 6.6 6.6l2.2-2.2c.3-.3.7-.4 1-.2 1.1.4 2.3.6 3.6.6.6 0 1 .4 1 1V20c0 .6-.4 1-1 1A17 17 0 0 1 3 4c0-.6.4-1 1-1h3.5c.6 0 1 .4 1 1 0 1.3.2 2.5.6 3.6.1.3 0 .7-.2 1z"/>
      </svg>
      <span>0417 552 308</span>
    </div>
    <div class="services-heading">
      <span class="rule"></span>
      <h2>SERVICES</h2>
      <span class="rule"></span>
    </div>
    <ul class="service-list">
      <li>Bulk fertilizer including Lime, Gypsum, Manure &amp; Compost.</li>
      <li>Granular fertilizer including Single Super,<br>Urea, Gran-am, &amp; Custom Blends.</li>
      <li>Modern equipment - Autosteer &amp; Variable Rate Capable.</li>
      <li>Friendly &amp; Reliable Service.</li>
    </ul>
  </section>

</main>
</body>
</html>
```